Local water manufacturing needs a re-design to an existing label design.

We need to change an existing label design for an established water manufacturing company located in the Bahamas. We are expanding into a new 1.5L size product and would like to do so with an updated label design that incorporates an animated pink conch shell (sample included) with at least one other bright color to match the existing blue background and the pink conch shell. The final design should convey an island feel and vibe. The existing label is only a suggestion. The entire label can be completely changed.

Target Market(s)

Hotels, tourist

Industry/Entity Type

Water Manufacturing

Requirements
Must have
• Bright color that matches blue cap and pink conch shell
Nice to have
• Simple design with sleek modern look.

```html
<!DOCTYPE html>
<html lang="en">
<head>
<meta charset="UTF-8">
<title>Coralis Filtered Water – 1.5 L Label</title>
<link rel="stylesheet" href="https://fonts.googleapis.com/css2?family=Fraunces:opsz,wght@144,600&family=Montserrat:wght@400;500;700&display=swap">
<style>
  :root {
    --aqua-top: #a6d8e0;
    --mist: #c9c8d2;
    --blush: #d9b3bf;
    --dusk: #9aa6b8;
    --deep-teal: #2f6f86;
    --ink: #4a4a4c;
    --white: #ffffff;
    --white-soft: rgba(255, 255, 255, 0.85);
    --shell-aqua: #3fb6cf;
    --shell-pink: #e9718f;
  }
  * { margin: 0; padding: 0; box-sizing: border-box; }
  html, body {
    width: 1200px;
    height: 1200px;
    overflow: hidden;
  }
  body {
    font-family: "Montserrat", sans-serif;
  }
  .label {
    position: relative;
    width: 1200px;
    height: 1200px;
    background: linear-gradient(180deg,
      var(--aqua-top) 0%,
      var(--mist) 28%,
      var(--blush) 42%,
      var(--dusk) 66%,
      var(--deep-teal) 100%);
    display: flex;
    flex-direction: column;
    align-items: center;
    color: var(--white);
    text-align: center;
  }
  .brand-name {
    margin-top: 230px;
    font-family: "Fraunces", serif;
    font-weight: 600;
    font-size: 130px;
    letter-spacing: -3px;
    color: var(--ink);
    line-height: 1;
  }
  .shell-art {
    margin-top: 70px;
    width: 300px;
    height: 260px;
    border-radius: 150px 150px 40px 40px;
    background: linear-gradient(180deg, var(--shell-aqua) 0%, #8f9fc4 55%, var(--shell-pink) 100%);
    box-shadow: 0 0 18px rgba(255,255,255,0.5);
  }
  .product-type {
    margin-top: 60px;
    font-weight: 700;
    font-size: 54px;
    line-height: 1.1;
    letter-spacing: 2px;
  }
  .wave-art {
    margin-top: 10px;
    width: 420px;
    height: 60px;
    border-radius: 30px;
    background: linear-gradient(90deg, rgba(255,255,255,0) 0%, rgba(255,255,255,0.22) 50%, rgba(255,255,255,0) 100%);
  }
  .claim {
    margin-top: 36px;
    font-weight: 500;
    font-size: 22px;
    letter-spacing: 1px;
  }
  .claim-detail {
    margin-top: 14px;
    font-weight: 400;
    font-size: 18px;
    line-height: 1.35;
    color: var(--white-soft);
  }
  .volume {
    margin-top: 54px;
    font-weight: 400;
    font-size: 16px;
    color: var(--white-soft);
  }
</style>
</head>
<body>
  <main class="label">
    <h1 class="brand-name">Coralis</h1>
    <div class="shell-art" role="img" aria-label="Illustrated scallop-style conch shell in aqua fading to pink"></div>
    <h2 class="product-type">FILTERED<br>WATER</h2>
    <div class="wave-art" role="img" aria-label="Soft white flowing wave lines"></div>
    <p class="claim">MINERALS ADDED</p>
    <p class="claim-detail">Enhanced with essential minerals<br>for a crisp, refreshing taste</p>
    <p class="volume">1.5 Liter</p>
  </main>
</body>
</html>
```